Finiding oppertunites in Real Estate 6.15.20

size of ad 7” x 9.6”
1-I like the ad to stand out and attract people's attention.
2-you should be able to see the text of the ad clearly .. see the attachment anything in yellow is instructions.
3-the list of topics should not be the main part of the ad
4-if you decide you want a picture or vector of a person .. (you decide)
then it should be a white male about 25-30 years old wearing a solid white or blue shirt and not long hair.
5-leave 1 inch for footer
see attachment
Good luck

Target Market(s)

potential male students 25-35 years of age

Industry/Entity Type

Education

Requirements
Must have
• will stand out and people would want to see it.
should be able to read the words of ad
Nice to have
• how to make money in real estate on one line

```html
<!DOCTYPE html>
<html lang="en">
<head>
<meta charset="UTF-8">
<title>Real Estate Career Course</title>
<link href="https://fonts.googleapis.com/css2?family=Open+Sans:wght@300;400;600;700;800&display=swap" rel="stylesheet">
<style>
  :root {
    --backdrop: #ecebe8;
    --paper: #ffffff;
    --ink: #555555;
    --ink-dark: #3e3e3e;
    --blue: #00a9ea;
    --red: #ee4a56;
    --red-light: #f2676f;
    --pattern-grey: #d9d9d9;
    --photo-brick: #8e3b2f;
    --photo-gold: #c9a54a;
  }
  * { margin: 0; padding: 0; box-sizing: border-box; }
  html, body {
    width: 1200px;
    height: 1200px;
    overflow: hidden;
    background: var(--backdrop);
    font-family: "Open Sans", sans-serif;
    color: var(--ink);
  }
  .flyer {
    position: absolute;
    left: 190px;
    top: 38px;
    width: 820px;
    height: 1124px;
    background: var(--paper);
    overflow: hidden;
  }
  .flyer__pattern {
    position: absolute;
    right: 0;
    top: 0;
    width: 430px;
    height: 760px;
    background: radial-gradient(ellipse at 85% 20%, var(--pattern-grey) 0%, rgba(217,217,217,0.55) 35%, rgba(255,255,255,0) 72%);
  }
  .centered {
    position: absolute;
    left: 0;
    width: 100%;
    text-align: center;
    white-space: nowrap;
  }
  .title {
    top: 92px;
    font-size: 46px;
    font-weight: 700;
    color: var(--ink);
    letter-spacing: 0.3px;
  }
  .headline {
    top: 160px;
    font-size: 47px;
    line-height: 56px;
    font-weight: 300;
    color: var(--ink);
  }
  .headline .accent { font-weight: 700; color: var(--blue); }
  .headline .strong { font-weight: 700; color: var(--ink-dark); }
  .tagline {
    position: absolute;
    right: 258px;
    text-align: right;
    font-weight: 600;
    color: var(--ink-dark);
    white-space: nowrap;
  }
  .tagline .accent { color: var(--blue); }
  .tagline--audience { top: 291px; font-size: 19px; line-height: 24px; }
  .tagline--knowledge { top: 370px; font-size: 20px; line-height: 28px; right: 264px; }
  .badge-remote {
    position: absolute;
    left: 298px;
    top: 459px;
    width: 216px;
    height: 43px;
    border-radius: 12px;
    background: linear-gradient(var(--red-light), var(--red));
    border: 1px solid #d83a47;
    color: #fff;
    font-size: 19px;
    font-weight: 700;
    line-height: 41px;
    text-align: center;
  }
  .sessions {
    top: 514px;
    font-size: 36px;
    font-weight: 800;
    color: var(--ink);
  }
  .start-date {
    position: absolute;
    left: 182px;
    top: 578px;
    width: 448px;
    height: 65px;
    border: 1.5px solid var(--ink-dark);
    border-radius: 12px;
    overflow: hidden;
    display: flex;
  }
  .start-date__label {
    width: 292px;
    font-size: 32px;
    font-weight: 700;
    color: var(--ink);
    line-height: 62px;
    text-align: center;
  }
  .start-date__value {
    flex: 1;
    background: var(--blue);
    color: #fff;
    font-size: 32px;
    font-weight: 700;
    line-height: 62px;
    text-align: center;
  }
  .hero-photo {
    position: absolute;
    left: 225px;
    top: 675px;
    width: 371px;
    height: 206px;
    border-radius: 6px;
    background: linear-gradient(100deg, var(--photo-brick) 0%, #a14a3b 55%, var(--photo-gold) 80%, #e0c880 100%);
  }
  .topics-heading {
    top: 906px;
    font-size: 24px;
    font-weight: 600;
    color: var(--blue);
  }
  .topics-rule {
    position: absolute;
    left: 388px;
    top: 945px;
    width: 43px;
    height: 4px;
    background: var(--ink);
  }
  .topics-list {
    position: absolute;
    left: 115px;
    top: 962px;
    width: 590px;
    font-size: 13px;
    line-height: 17.5px;
    text-align: center;
    color: var(--ink-dark);
  }
</style>
</head>
<body>
  <main class="flyer">
    <div class="flyer__pattern" role="img" aria-label="Soft grey dotted diamond pattern"></div>

    <h1 class="centered title">Real Estate Career Course</h1>

    <h2 class="centered headline">How to <span class="accent">Make Money</span><br>in <span class="strong">Real Estate?</span></h2>

    <p class="tagline tagline--audience">For those who have started or<br>would like to go into <span class="accent">Real Estate</span></p>

    <p class="tagline tagline--knowledge">An investment in knowledge<br>opens up untold <span class="accent">opportunities</span></p>

    <div class="badge-remote">Remote sessions</div>

    <p class="centered sessions">12 session course</p>

    <div class="start-date">
      <span class="start-date__label">Classes starting</span>
      <span class="start-date__value">June 16</span>
    </div>

    <div class="hero-photo" role="img" aria-label="Photo of a model brick house with stacks of gold coins"></div>

    <h3 class="centered topics-heading">A partial listing of Topics</h3>
    <div class="topics-rule"></div>

    <p class="topics-list">Single-family | Multifamily | Management | Real Estate Concepts | Real Estate law | Investment properties | Foreclosures Rehab | &nbsp;Foreclosures | Short sales | Development | Finical modeling<br>HUD properties | Due Diligence e</p>
  </main>
</body>
</html>
```